"Harbor Builders" is a residential building company and needs a new business card design and may re

We would like a redesign based on the existing logo, and would like to see a new font as well. We are bespoke home builders who build sustainable energy efficient homes.

Industry/Entity Type

Construction

Contact Information for Business Card

Business card size 40mm x 90mm

Colors

Designer to choose colors to be used in the design.

```html
<!DOCTYPE html>
<html lang="en">
<head>
<meta charset="utf-8">
<title>Harbor Builders – Business Card</title>
<link rel="stylesheet" href="https://fonts.googleapis.com/css2?family=Oswald:wght@600&family=Work+Sans:wght@400;500&display=swap">
<style>
  :root {
    --backdrop: #2b2b2d;
    --card: #1d1d1e;
    --card-edge: #262628;
    --brand-blue: #2f4aa8;
    --brand-orange: #f0842a;
    --text-light: #e9e9e9;
  }
  * { box-sizing: border-box; margin: 0; padding: 0; }
  html, body { width: 1200px; height: 900px; overflow: hidden; }
  body {
    background: var(--backdrop);
    font-family: "Work Sans", Arial, sans-serif;
    color: var(--text-light);
    position: relative;
  }
  .card {
    position: absolute;
    left: 250px;
    width: 700px;
    height: 400px;
    background: linear-gradient(135deg, var(--card) 0%, var(--card-edge) 100%);
    box-shadow: 0 14px 30px rgba(0,0,0,.45);
  }
  .card--front { top: 30px; }
  .card--back { top: 470px; }

  /* front */
  .brand {
    position: absolute;
    left: 50%; top: 50%;
    transform: translate(-50%, -50%);
    display: flex; align-items: center; gap: 18px;
  }
  .brand__square { width: 34px; height: 34px; background: var(--brand-orange); }
  .brand__name {
    font-weight: 500;
    font-size: 44px;
    letter-spacing: 2px;
    color: var(--brand-orange);
    white-space: nowrap;
  }

  /* back */
  .registration {
    position: absolute;
    right: 48px; top: 48px;
    text-align: right;
    font-size: 17px;
    line-height: 1.3;
  }
  .registration .label { color: var(--brand-orange); }

  .details {
    position: absolute;
    left: 50px; top: 148px;
    display: flex;
    align-items: center;
    gap: 20px;
  }

  .person { text-align: right; white-space: nowrap; }
  .person__name {
    font-family: "Oswald", "Arial Narrow", sans-serif;
    font-weight: 600;
    font-size: 40px;
    line-height: 1;
    color: var(--brand-blue);
    text-transform: uppercase;
    letter-spacing: .5px;
  }
  .person__role { font-size: 19px; margin-top: 6px; }

  .divider {
    width: 3px; height: 68px;
    background: var(--brand-orange);
    flex: none;
  }

  .contacts {
    list-style: none;
    font-size: 17px;
    line-height: 1.45;
    white-space: nowrap;
  }
  .contacts li { display: flex; align-items: center; gap: 12px; }
  .contacts svg { width: 15px; height: 15px; flex: none; }
  .contacts .highlight { color: var(--brand-orange); }

  .address {
    position: absolute;
    left: 120px; bottom: 46px;
    font-size: 19px;
    letter-spacing: .3px;
  }
</style>
</head>
<body>

<section class="card card--front" aria-label="Card front">
  <div class="brand">
    <span class="brand__square"></span>
    <span class="brand__name">Harbor Builders</span>
  </div>
</section>

<section class="card card--back" aria-label="Card back">
  <p class="registration">
    <span class="label">Registration</span>-30481<br>
    <span class="label">ABN:</span> 41 203 665 817
  </p>

  <div class="details">
    <div class="person">
      <h1 class="person__name">Daniel Moretti</h1>
      <p class="person__role">Founder</p>
    </div>

    <span class="divider"></span>

    <ul class="contacts">
      <li>
        <svg viewBox="0 0 16 16" aria-hidden="true"><path d="M4 1.5l2.3 3-1.4 1.6c.8 1.9 2.3 3.4 4.2 4.2l1.6-1.4 3 2.3-1.3 2.3C7 13.5 2.5 9 2 3z" fill="var(--brand-orange)"/></svg>
        <span>0400 555 018</span>
      </li>
      <li>
        <svg viewBox="0 0 16 16" aria-hidden="true"><rect x="1" y="3" width="14" height="10" fill="var(--brand-orange)"/><path d="M1 3l7 6 7-6" fill="none" stroke="var(--card)" stroke-width="1.4"/></svg>
        <span>daniel@harborbuilders.com.au</span>
      </li>
      <li>
        <svg viewBox="0 0 16 16" aria-hidden="true" fill="none" stroke="var(--brand-orange)" stroke-width="1.4"><circle cx="8" cy="8" r="6.5"/><ellipse cx="8" cy="8" rx="2.8" ry="6.5"/><path d="M1.5 8h13M2.5 5h11M2.5 11h11"/></svg>
        <span>www.<span class="highlight">harborbuilders.com</span>.au</span>
      </li>
    </ul>
  </div>

  <p class="address">PO Box 2210 Eastgate LPO Kelmscott WA 6111</p>
</section>

</body>
</html>
```